AUTO SPAREPART DISTRIBUTOR BUSINESS CARD

Our company need a business card design. We are a distributor and importer of car spareparts for VORN and PELTARO car model. We would like the design with White color back ground and attractive color for the fonts and looks clean, simple and attractive.
We provide the company information and the brand logo (VORN, PELTARO, ZUM, 738) should be put on the business card.

Thank you

Target Market(s)

Auto spareparts retailer shop and supplier.

Industry/Entity Type

Business

Contact Information for Business Card

The front side of the business card only contain company informations, and the back side may be put the brand logo (VORN, PELTARO, ZUM AND 738).

Requirements
Must have
• On the back side ( the brand logo) position , should have a transparency world map picture ( i uploaded the world map picture sample ).
• Also, need to put some words of " AUTO PARTS DISTRIBUTOR " (may be put on any appropriate place).

```html
<!DOCTYPE html>
<html lang="en">
<head>
<meta charset="utf-8">
<title>ZUM Auto Parts Distributor – Business Card</title>
<link rel="stylesheet" href="https://fonts.googleapis.com/css2?family=Lato:wght@100;300;400;700&display=swap">
<style>
  :root {
    --stage: #ececec;
    --brand-green: #689f42;
    --map-green: #57883a;
    --ink-dark: #2a2a2a;
    --ink-grey: #6d6d6d;
    --card-white: #ffffff;
    --band-black: #0d0d0d;
  }
  * { box-sizing: border-box; margin: 0; padding: 0; }
  html, body { width: 1200px; height: 586px; overflow: hidden; }
  body {
    background: var(--stage);
    font-family: "Lato", Arial, sans-serif;
    position: relative;
  }
  .card {
    position: absolute;
    top: 125px;
    width: 502px;
    height: 295px;
    overflow: hidden;
  }

  /* ---------- Front: company side ---------- */
  .card--front { left: 61px; background: var(--brand-green); }
  .world-map {
    position: absolute;
    left: 36px; top: 47px;
    width: 428px; height: 218px;
    background: radial-gradient(ellipse at center, var(--map-green) 0%, rgba(87,136,58,0.55) 60%, rgba(87,136,58,0) 100%);
    border-radius: 40px;
  }
  .front-wordmark {
    position: absolute;
    left: 0; right: 0; top: 100px;
    text-align: center;
    font-weight: 100;
    font-size: 88px;
    letter-spacing: 6px;
    color: var(--ink-dark);
    line-height: 1;
  }
  .tagline {
    position: absolute;
    left: 55px; right: 55px; top: 268px;
    display: flex; align-items: center; gap: 10px;
    color: #f2f2f2;
    font-weight: 300;
    font-size: 12.5px;
    letter-spacing: 0.3px;
    white-space: nowrap;
  }
  .tagline::before, .tagline::after {
    content: ""; flex: 1; height: 2px; background: var(--band-black);
  }

  /* ---------- Back: contact side ---------- */
  .card--back { left: 618px; background: var(--card-white); }
  .back-wordmark {
    position: absolute;
    left: 70px; top: 98px;
    width: 120px;
    text-align: center;
    font-weight: 300;
    font-size: 48px;
    letter-spacing: 3px;
    color: var(--brand-green);
  }
  .person {
    position: absolute; right: 28px; top: 42px; text-align: right;
  }
  .person__name { color: var(--brand-green); font-weight: 300; font-size: 17px; }
  .person__role { color: var(--ink-grey); font-weight: 300; font-size: 12px; margin-top: 2px; }
  .contacts {
    position: absolute; right: 28px; top: 98px;
    list-style: none;
  }
  .contacts li {
    display: flex; justify-content: flex-end; align-items: center;
    height: 22px;
    font-size: 11.5px; font-weight: 400; color: var(--ink-dark);
  }
  .contacts svg { width: 12px; height: 12px; margin-left: 9px; fill: var(--brand-green); }
  .address-band {
    position: absolute; left: 0; bottom: 0;
    width: 316px; height: 45px;
    background: var(--brand-green);
    clip-path: polygon(0 0, 248px 0, 316px 100%, 0 100%);
    color: #fff; font-weight: 300; font-size: 11.5px; line-height: 17px;
    padding: 5px 0 0 15px;
  }
  .black-band {
    position: absolute; right: 0; bottom: 0;
    width: 160px; height: 17px;
    background: var(--band-black);
    clip-path: polygon(0 0, 100% 0, 100% 100%, 18px 100%);
  }
  .partners {
    position: absolute; top: 252px; left: 294px;
    display: flex;
  }
  .partner {
    width: 64px;
    text-align: center;
    font-weight: 700;
    font-size: 10.5px;
    letter-spacing: 0.3px;
    color: var(--ink-dark);
  }
</style>
</head>
<body>

<section class="card card--front" aria-label="Company side">
  <div class="world-map" role="img" aria-label="Dotted world map in darker green tones"></div>
  <div class="front-wordmark">ZUM</div>
  <div class="tagline">AUTO PARTS DISTRIBUTOR</div>
</section>

<section class="card card--back" aria-label="Contact side">
  <div class="back-wordmark">ZUM</div>

  <div class="person">
    <div class="person__name">RIAN TANU</div>
    <div class="person__role">Director</div>
  </div>

  <ul class="contacts">
    <li>rian.tanu22 <svg viewBox="0 0 12 12"><circle cx="6" cy="6" r="6"/></svg></li>
    <li>+62-21-55501234 <svg viewBox="0 0 12 12"><path d="M1 5c0-2 2-3 5-3s5 1 5 3H8.5V4h-5v1zM3 6h6l1.5 5h-9z"/></svg></li>
    <li>+62-21-55501235 <svg viewBox="0 0 12 12"><path d="M3 1h6v3H3zM1 5h10v4H9V7H3v2H1zM3.5 8h5v3h-5z"/></svg></li>
    <li>+62-812000478 <svg viewBox="0 0 12 12"><path d="M3.5 0h5a1 1 0 0 1 1 1v10a1 1 0 0 1-1 1h-5a1 1 0 0 1-1-1V1a1 1 0 0 1 1-1zM4 1.5v8h4v-8z"/></svg></li>
    <li>zumparts-office@mail.com <svg viewBox="0 0 12 12"><path d="M0 2h12v8H0zM1 3l5 4 5-4z" fill-rule="evenodd"/></svg></li>
  </ul>

  <div class="partners">
    <span class="partner">PELTARO</span>
    <span class="partner">VORN</span>
    <span class="partner">738</span>
  </div>

  <div class="black-band"></div>
  <div class="address-band">Taman Kenari 4, Blok c-07 No. B-18 ,<br>Kalideres Timur, Jakarta Barat, Indonesia (11840)</div>
</section>

</body>
</html>
```